National online rug retailer needs a home page design

See the FloorNest logo and create a home page design around that color theme. Details are spelled out in word document uploaded below.

Apparently this website did not take my attachement showing the logo and basic requirements.  If you would send me your email address, I will send you the attachment directly.
Best regards,
Tom Vance
tvance@mrdcorp.example

Target Market(s)

The target market is home owners 25 to 75 years old with combined incomes over $100,000 per year.

Industry/Entity Type

Online

Requirements
Must have
• Lots of white space with black letters and creative use of red and possibly one other color. Would like a compelling call to action button.

```html
<!DOCTYPE html>
<html lang="en">
<head>
<meta charset="utf-8">
<title>FloorNest – Home</title>
<link rel="stylesheet" href="https://fonts.googleapis.com/css2?family=PT+Sans:wght@400;700&family=PT+Sans+Narrow:wght@400;700&display=swap">
<style>
:root{
  --red:#c8121b;
  --red-dark:#a30c12;
  --red-deep:#8e0a0f;
  --orange:#f8a11c;
  --ink:#222;
  --muted:#555;
  --line:#e2e2e2;
  --panel:#f3f3f3;
  --white:#fff;
}
*{box-sizing:border-box;margin:0;padding:0}
html,body{width:1026px;height:1200px;overflow:hidden}
body{position:relative;background:var(--white);font-family:"PT Sans",sans-serif;color:var(--ink);font-size:12px}
a{color:inherit;text-decoration:none}
.abs{position:absolute}

.topbar{left:0;top:0;width:1026px;height:31px;background:var(--red-dark)}
.topbar p{position:absolute;left:675px;top:9px;color:#fff;font-size:10.5px}
.topstrip{left:0;top:31px;width:1026px;height:225px;background:#f6f6f6;border-top:8px solid #ececec}

.brand{left:96px;top:52px;display:flex;align-items:center;gap:8px}
.brand-mark{width:24px;height:24px;background:var(--red)}
.brand-name{font-size:36px;font-weight:400;color:var(--red);letter-spacing:-.5px;line-height:1}

.search{left:374px;top:60px;width:226px;height:28px;display:flex}
.search span{flex:1;background:#f0f0f0;border:1px solid #ddd;font-size:10px;font-style:italic;color:#777;padding:7px 10px}
.search i{width:34px;background:var(--orange);display:flex;align-items:center;justify-content:center}

.tollfree{left:637px;top:50px;font-size:16px;color:#111}
.tollfree b{font-weight:400;color:var(--red)}
.acct{left:637px;top:80px;display:flex;gap:4px}
.acct span{background:#e9e9e9;border-bottom:2px solid #d4d4d4;height:24px;padding:0 8px;font-size:11px;line-height:24px;color:#333}
.acct .chat::before{content:"";display:inline-block;width:6px;height:6px;border-radius:50%;background:var(--red);margin-right:6px;vertical-align:1px}

.nav{left:95px;top:119px;width:818px;height:48px;background:linear-gradient(var(--red),var(--red-dark));display:flex;border-radius:2px}
.nav a{color:#fff;font-size:13px;line-height:48px;text-align:center;border-right:1px solid rgba(0,0,0,.18)}
.nav a:last-child{border:0}
.nav .on{background:var(--orange)}

.browse{left:98px;top:182px;width:199px}
.browse h3{font-family:"PT Sans Narrow",sans-serif;font-weight:400;font-size:17px;color:var(--red);padding:6px 12px;border:1px solid #eee;border-bottom:0}
.browse .theme{background:var(--red);color:#fff;font-size:11px;padding:0 20px;height:33px;line-height:33px;border-left:4px solid var(--orange)}
.browse ul{list-style:none;background:var(--panel);padding:6px 4px 6px 18px}
.browse li{font-size:11px;line-height:15px;padding:5px 0 5px 24px;border-bottom:1px dotted #bbb;position:relative}
.browse li:last-child{border:0}
.browse li::before{content:"→";position:absolute;left:8px;font-size:8px;top:5px}
.facet{height:33px;margin-top:2px;border:1px solid #ddd;border-left:3px solid var(--red);background:linear-gradient(#fff,#ececec);font-size:11px;line-height:31px;padding-left:18px}

.about{left:98px;top:594px;width:199px;height:306px;border:1px solid #eee;padding:12px 10px}
.about h3{font-weight:400;font-size:15px;color:var(--red);margin-bottom:10px}
.about p{font-size:9.4px;line-height:15.4px;color:var(--muted);text-align:justify;margin-bottom:14px}
.btn-orange{display:inline-block;background:var(--orange);color:#fff;font-family:"PT Sans Narrow",sans-serif;font-weight:700;font-size:13px;padding:5px 10px;float:right;margin-right:6px}

.hero{left:308px;top:182px;width:607px;height:291px;border:1px solid #eee;padding:13px 12px}
.hero-img{width:580px;height:265px;background:radial-gradient(ellipse at 50% 45%,#e8d4b6 0,#c99d74 30%,#7a1a1f 52%,#5a2a1a 100%);position:relative}
.caption{position:absolute;left:0;bottom:0;width:100%;height:38px;background:rgba(0,0,0,.55);color:#fff;font-family:"PT Sans Narrow",sans-serif;font-size:14px;line-height:38px;padding-left:13px}
.dots{position:absolute;right:20px;top:14px;display:flex;gap:4px}
.dots i{width:10px;height:10px;border-radius:50%;background:#f6e7a5}
.dots i:last-child{background:var(--red);border:1px solid #fff}

.section-title{left:322px;top:483px;font-size:24px;color:var(--red)}
.arrows{left:633px;top:494px;display:flex;gap:8px}
.arrows i{width:20px;height:20px;border-radius:50%;border:1px solid #ccc;background:#f4f4f4;font-style:normal;font-size:10px;color:#aaa;text-align:center;line-height:18px}

.card{width:181px;height:177px;background:var(--panel);border:1px solid #e4e4e4;padding:10px 9px;box-shadow:0 4px 4px -3px rgba(0,0,0,.18)}
.card .thumb{height:80px;border-radius:6px}
.card h4{font-weight:400;font-size:11px;margin:10px 0 4px 2px}
.card .price{font-size:11px;color:var(--red);margin-left:3px}
.buy{display:inline-block;margin:8px 0 0 6px;width:84px;height:25px;background:linear-gradient(#555,#111);color:#fff;font-family:"PT Sans Narrow",sans-serif;font-weight:700;font-size:12.5px;text-align:center;line-height:25px;border-radius:2px}

.also{left:708px;top:497px;width:206px;height:404px;background:var(--red-dark);padding:0 11px}
.also h3{font-family:"PT Sans Narrow",sans-serif;font-weight:400;font-size:16px;color:#fff;padding:5px 3px;height:30px}
.also .card{position:static;width:184px;margin-bottom:12px;box-shadow:none}

.footer{left:0;top:928px;width:1026px;height:272px;background:linear-gradient(var(--red),var(--red-deep))}
.fcol{top:951px;color:#fff}
.fcol h4{font-family:"PT Sans Narrow",sans-serif;font-weight:400;font-size:15px;margin-bottom:9px}
.fcol li{list-style:none;font-size:10.5px;line-height:15.4px}
.pay{left:443px;top:1060px;width:197px;height:78px;background:#fff;border-radius:3px;padding:10px 12px;display:grid;grid-template-columns:repeat(6,1fr);gap:6px}
.pay i{background:#dcdce4;border-radius:2px;height:18px}
.pay i:nth-child(n+7){height:24px;border-radius:50%;background:#e3dcc0}
.social{left:699px;top:979px;display:flex;gap:10px}
.social i{width:24px;height:22px;background:#f2f2f2;opacity:.9;border-radius:2px}
.field{width:140px;height:27px;border-radius:14px;background:#fff;font-size:10px;color:#666;padding:7px 24px}
.submit{left:846px;top:1094px;width:70px;height:33px;background:linear-gradient(#444,#111);color:#fff;border:1px solid #888;border-radius:3px;font-family:"PT Sans Narrow",sans-serif;font-weight:700;font-size:13px;text-align:center;line-height:31px}
.copy{left:0;top:1166px;width:1026px;text-align:center;color:#fff;font-size:9.5px}
</style>
</head>
<body>
<div class="abs topbar"><p>Items: ___ | Total $0.00 | View Cart | Checkout</p></div>
<div class="abs topstrip"></div>

<div class="abs brand"><span class="brand-mark"></span><span class="brand-name">FloorNest.com</span></div>

<div class="abs search"><span>enter key words or item #</span>
  <i><svg width="16" height="16" viewBox="0 0 16 16"><circle cx="7" cy="7" r="4.5" fill="none" stroke="#fff" stroke-width="2"/><path d="M10.5 10.5L14 14" stroke="#fff" stroke-width="2.2"/></svg></i></div>

<div class="abs tollfree">Order Toll-Free: <b>1-888-555-0142</b></div>
<div class="abs acct"><span>MY ACCOUNT</span><span>SIGN IN</span><span class="chat">LIVE CHAT ONLINE</span></div>

<nav class="abs nav">
  <a class="on" style="width:89px">Home</a><a style="width:145px">Selection guides</a><a style="width:101px">Rug Care</a><a style="width:73px">FAQ</a><a style="width:127px">Return Policy</a><a style="width:119px">Free Shipping</a><a style="flex:1">Clearance Rugs</a>
</nav>

<aside class="abs browse">
  <h3>BROWSE</h3>
  <div class="theme">RUG THEME</div>
  <ul><li>Traditional</li><li>Transitional</li><li>Casual</li></ul>
  <div class="facet">COLOR WAY</div>
  <div class="facet">SIZE</div>
  <div class="facet">SHAPE</div>
  <div class="facet">FIBER CONTENT</div>
  <div class="facet">MFGR. BRAND</div>
  <div class="facet">MFGR.COLLECTION</div>
  <div class="facet">PRICE</div>
</aside>

<section class="abs about">
  <h3>About FloorNest</h3>
  <p>Sed ut perspiciatis unde omnis iste natus error sit voluptatem accusantium doloremque laudantium, totam rem aperiam, eaque ipsa quae ab illo inventore veritatis et quasi architecto beatae vitae dicta sunt explicabo.</p>
  <p>aut fugit, sed quia consequuntur magni dolores eos qui ratione voluptatem sequi nesciunt. Neque porro quisquam est, qui dolorem ipsum quia dolor sit amet. Nemo enim ipsam voluptatem quia quisquam est, qui dolorem ipsum quia dolor sit amet.</p>
  <a class="btn-orange">Read More</a>
</section>

<section class="abs hero">
  <div class="hero-img" role="img" aria-label="Photo of an ornate red and cream traditional rug on a wooden floor">
    <div class="caption">SELECTED OUTDOOR COLLECTIONS 15% OFF<span class="dots"><i></i><i></i><i></i></span></div>
  </div>
</section>

<h2 class="abs section-title" style="font-weight:400">Rugs</h2>
<div class="abs arrows"><i>‹</i><i>›</i></div>

<div class="abs card" style="left:316px;top:528px"><div class="thumb" role="img" aria-label="Rolled red and grey patterned rugs" style="background:linear-gradient(135deg,#4a3a2c,#b4442e 55%,#9a8f86)"></div><h4>Tribal Rugs</h4><div class="price">Price : $60.00 - $ 500.20</div><a class="buy">Buy Now</a></div>
<div class="abs card" style="left:514px;top:528px"><div class="thumb" role="img" aria-label="Dark rug with colourful ring pattern" style="background:linear-gradient(135deg,#2d2418,#6a5a3a 50%,#2d2418)"></div><h4>Tribal Rugs</h4><div class="price">Price : $60.00 - $ 500.20</div><a class="buy">Buy Now</a></div>
<div class="abs card" style="left:316px;top:724px"><div class="thumb" role="img" aria-label="Purple rug with geometric squares" style="background:linear-gradient(135deg,#7a3d9a,#5b2a78)"></div><h4>Tribal Rugs</h4><div class="price">Price : $60.00 - $ 500.20</div><a class="buy">Buy Now</a></div>
<div class="abs card" style="left:514px;top:724px"><div class="thumb" role="img" aria-label="Rug with wavy multicoloured stripes" style="background:linear-gradient(135deg,#8a4a2a,#c9a77a 45%,#5a3a3a)"></div><h4>Tribal Rugs</h4><div class="price">Price : $60.00 - $ 500.20</div><a class="buy">Buy Now</a></div>

<section class="abs also">
  <h3>YOU MAY ALSO LIKE</h3>
  <div class="card"><div class="thumb" role="img" aria-label="Red tribal rug with dense motif border" style="background:linear-gradient(#b8231e,#6a1812)"></div><h4>Tribal Rugs</h4><div class="price">Price : $60.00 - $ 500.20</div><a class="buy">Buy Now</a></div>
  <div class="card"><div class="thumb" role="img" aria-label="Black, cream and gold chevron rug" style="background:linear-gradient(135deg,#3a2a20,#d9cfae 50%,#3a2a20)"></div><h4>Tribal Rugs</h4><div class="price">Price : $60.00 - $ 500.20</div><a class="buy">Buy Now</a></div>
</section>

<footer class="abs footer"></footer>
<div class="abs fcol" style="left:95px"><h4>Customer Service</h4><ul><li>Shipping</li><li>Return Policy</li><li>Privacy Policy</li><li>Ordering &amp; Delivery Checklist</li><li>Terms of Use</li><li>Terms of Sale</li><li>Contact Us</li><li>Environmental Policy</li></ul></div>
<div class="abs fcol" style="left:275px"><h4>Resources</h4><ul><li>Product Articles</li><li>Learning Center</li><li>Help</li><li>Refer A Friend</li><li>FloorNest Blog</li><li>Room Scene Viewer</li><li>Site Map</li><li>FAQ</li><li>Customer Testimonials</li><li>Photo Gallery</li></ul></div>
<div class="abs fcol" style="left:447px"><h4>Corporate Info</h4><ul><li>About FloorNest.com</li><li>Careers</li><li>Affiliates</li></ul></div>
<div class="abs fcol" style="left:447px;top:1036px"><h4>Payments</h4></div>
<div class="abs pay" aria-label="Accepted payment methods and security seals"><i></i><i></i><i></i><i></i><i></i><i></i><i></i><i></i><i></i><i></i><i></i><i></i></div>
<div class="abs fcol" style="left:696px"><h4>Connect With Us</h4></div>
<div class="abs social" aria-label="Social links"><i></i><i></i><i></i><i></i><i></i><i></i></div>
<div class="abs fcol" style="left:696px;top:1030px"><h4>Email Signup</h4></div>
<div class="abs field" style="left:697px;top:1056px">Enter Your Name</div>
<div class="abs field" style="left:698px;top:1096px">Enter Your Email</div>
<div class="abs submit">SUBMIT</div>
<div class="abs copy">© 2013 .FloorNest.com., All Rights Reserved</div>
</body>
</html>
```